Website for a Pittsburgh Musical Production

We are creating a website for a musical stage production. Content and copy is included below. We are targeting production in early 2023.

```html
<!DOCTYPE html>
<html lang="en">
<head>
<meta charset="utf-8">
<title>Hollowmoor – The Rock Opera</title>
<link href="https://fonts.googleapis.com/css2?family=Acme&family=Poppins:wght@400;500;600;700&display=swap" rel="stylesheet">
<style>
:root{
  --page:#0a1517;
  --panel:#070c0d;
  --contact:#0d1b1e;
  --footer:#091315;
  --green:#5e8a46;
  --white:#ffffff;
  --muted:#c9d0cf;
  --line:#3a4a4c;
}
*{margin:0;padding:0;box-sizing:border-box}
html,body{width:1200px;height:3165px;overflow:hidden;background:var(--page)}
body{position:relative;font-family:'Poppins',sans-serif;color:var(--white)}
.abs{position:absolute}

.hero{left:0;top:0;width:1200px;height:590px;
  background:radial-gradient(ellipse at 28% 45%,#2f3536 0%,#161d1e 35%,#0a1517 75%),#0a1517}
.hero-shade{left:0;top:0;width:1200px;height:590px;
  background:linear-gradient(180deg,rgba(0,0,0,.55) 0%,rgba(0,0,0,0) 20%,rgba(10,21,23,0) 70%,rgba(10,21,23,1) 100%)}

.brand{left:144px;top:36px;width:262px}
.brand-name{font-family:'Acme',sans-serif;color:var(--green);font-size:38px;line-height:44px;letter-spacing:.5px}
.brand-tag{font-family:'Poppins',sans-serif;color:var(--white);font-size:19px;text-align:right;line-height:24px;margin-top:2px}

.nav{top:64px;left:0;font-size:14.5px;font-weight:500;letter-spacing:.2px}
.nav a{position:absolute;color:var(--white);text-decoration:none;white-space:nowrap}
.nav a.active::after{content:"";position:absolute;left:-3px;right:-3px;top:24px;height:3px;background:var(--green);border-radius:2px}
.search{left:1009px;top:52px;width:44px;height:44px;border-radius:50%;background:var(--green)}

.about{left:144px;top:582px;width:912px;height:550px;background:var(--panel);text-align:center}
.about h2{font-family:'Acme',sans-serif;font-weight:400;font-size:56px;line-height:60px;position:absolute;top:70px;width:100%}
.about h3{font-family:'Acme',sans-serif;font-weight:400;color:var(--green);font-size:40px;line-height:44px;position:absolute;top:142px;width:100%}
.about p{position:absolute;left:78px;width:756px;top:216px;font-size:13.6px;line-height:24px;color:var(--muted)}

.btn{display:flex;align-items:center;justify-content:center;background:var(--green);border-radius:34px;color:var(--white);font-weight:700;font-size:20px;letter-spacing:-.2px;text-decoration:none}

.section-title{width:1200px;text-align:center;font-family:'Acme',sans-serif;font-size:56px;line-height:60px;font-weight:400}
.section-title span{color:var(--green)}

.tile{position:absolute}

.contact{left:0;top:2306px;width:1200px;height:607px;background:var(--contact)}
.field{position:absolute;border:1px solid var(--line);border-radius:2px;font-size:12.5px;color:var(--muted);padding:14px 25px}

.footer{left:0;top:2913px;width:1200px;height:252px;background:var(--footer)}
.social{position:absolute;top:2957px;width:52px;height:52px;border-radius:50%;border:1.5px solid var(--muted);
  display:flex;align-items:center;justify-content:center;font-size:10.5px;font-weight:600;color:var(--white);text-decoration:none}
.foot-nav{top:3042px;width:1200px;text-align:center;font-weight:700;font-size:25px;letter-spacing:-.2px}
.foot-nav .sep{margin:0 18px}
.copy{top:3100px;width:1200px;text-align:center;font-size:13px;color:var(--muted)}
</style>
</head>
<body>

<div class="abs hero" role="img" aria-label="Dark moody hero artwork with the show title in script lettering"></div>
<div class="abs hero-shade"></div>

<header>
  <div class="abs brand">
    <div class="brand-name">HOLLOWMOOR</div>
    <div class="brand-tag">THE ROCK OPERA</div>
  </div>
  <nav class="abs nav">
    <a class="active" href="#" style="left:541px">HOME</a>
    <a href="#" style="left:616px">ABOUT</a>
    <a href="#" style="left:697px">SERVICES</a>
    <a href="#" style="left:796px">PORTFOLIO</a>
    <a href="#" style="left:906px">CONTACT</a>
  </nav>
  <div class="abs search">
    <svg width="44" height="44" viewBox="0 0 44 44"><circle cx="20" cy="20" r="5.5" fill="none" stroke="#fff" stroke-width="2.4"/><line x1="24" y1="24" x2="28" y2="28" stroke="#fff" stroke-width="2.8" stroke-linecap="round"/></svg>
  </div>
</header>

<section class="abs about">
  <h2>ABOUT</h2>
  <h3>HOLLOWMOOR THE ROCK OPERA</h3>
  <p>Lorem ipsum dolor sit amet, consectetur adipiscing elit, sed do eiusmod tempor incididunt ut labore et dolore magna&nbsp; ipsum suspendisse ultrices g commodo viverra maecenas accumsan lacus vel facilisis. Lorem ipsum dolor sit amet, consectetur adipiscing elit, sed do eiusmod tempor incididunt ut labore et dolore magna&nbsp; ipsum suspendisse ultrices g commodo viverra maecenas accumsan lacus vel facilisis. Lorem ipsum dolor sit amet, consectetur adipiscing elit, sed do eiusmod tempor incididunt ut labore et dolore magna&nbsp; ipsum su spendisse ultrices g commodo viverra maecenas accumsan lacus vel facilisis.</p>
  <a class="abs btn" href="#" style="left:356px;top:404px;width:200px;height:66px">READ MORE</a>
</section>

<h2 class="abs section-title" style="top:1201px">OUR <span>PORTFOLIO</span></h2>

<div class="tile" style="left:12px;top:1303px;width:383px;height:406px;background:linear-gradient(180deg,#2a2c33 0%,#10131c 55%,#000 100%)" role="img" aria-label="Album cover artwork for a metal opera release"></div>
<div class="tile" style="left:408px;top:1303px;width:383px;height:406px;background:radial-gradient(ellipse at 50% 65%,#c9862a 0%,#7a1d1a 35%,#2a170f 70%,#140b07 100%)" role="img" aria-label="Album cover artwork in red and gold tones"></div>
<div class="tile" style="left:803px;top:1303px;width:383px;height:406px;background:linear-gradient(135deg,#4a3a3a 0%,#9a8074 40%,#2b2425 75%,#5a3b3d 100%)" role="img" aria-label="Album cover artwork: photo collage for an a cappella group"></div>
<div class="tile" style="left:12px;top:1719px;width:779px;height:407px;background:radial-gradient(ellipse at 22% 55%,#4c6a36 0%,#1f2a18 40%,#0d0f0b 75%)" role="img" aria-label="Show artwork in green tones with script show title"></div>
<div class="tile" style="left:803px;top:1719px;width:383px;height:407px;background:radial-gradient(ellipse at 55% 55%,#d77a5f 0%,#6b3f8a 40%,#3b3aa8 70%,#d6b23a 100%)" role="img" aria-label="Album cover artwork with painted flowers in bright colours"></div>

<a class="abs btn" href="#" style="left:500px;top:2165px;width:200px;height:66px">VIEW MORE</a>

<section class="abs contact">
  <h2 class="abs section-title" style="top:89px">CONTACT <span>FORM</span></h2>
  <div class="field" style="left:156px;top:202px;width:289px;height:50px">Enter Name</div>
  <div class="field" style="left:456px;top:202px;width:289px;height:50px">Enter Email</div>
  <div class="field" style="left:755px;top:202px;width:289px;height:50px">Phone</div>
  <div class="field" style="left:156px;top:267px;width:888px;height:146px;padding-top:16px">Message</div>
  <a class="abs btn" href="#" style="left:472px;top:444px;width:256px;height:66px">SUBMIT MESSAGE</a>
</section>

<footer class="abs footer"></footer>
<a class="social" href="#" style="left:477px">Kith</a>
<a class="social" href="#" style="left:541px">Chirpy</a>
<a class="social" href="#" style="left:605px">Workly</a>
<a class="social" href="#" style="left:669px">Reelo</a>
<nav class="abs foot-nav">HOME<span class="sep">/</span>ABOUT<span class="sep">/</span>SERVICES<span class="sep">/</span>PORTFOLIO<span class="sep">/</span>CONTACT</nav>
<div class="abs copy">© 2021 Hollowmoor the rock opera.All Rights Reserved &nbsp;|&nbsp; Privacy &nbsp;|&nbsp; Terms and Use</div>

</body>
</html>
```